Valmora Company needs a Business Card Design

We just opened our business recently and we need a business card design. Our basic product are clothes and accessories. We would like to see designs that use bright colors like pink, light blue and purple. In addition to that kindly include also our address in the business card which our main office is located in Los Angeles, California.
The final design should communicate that we have affordable price yet high quality brand.

Target Market(s)

young and middle age women

Industry/Entity Type

Business

Contact Information for Business Card

Valmora Apparel and Accessories 4873 North Bellcrest St. Los Angeles California
Tel: 555-318-6492

Logo Text

Valmora's Apparel and Accessories

Font styles to use
Serif

Requirements
Must have
• there should be a graphic of a sexy lady wearing an elegant dress at the upper left corner of the business card.

```html
<!DOCTYPE html>
<html lang="en">
<head>
<meta charset="utf-8">
<title>Valmora Apparel and Accessories – Business Card</title>
<link rel="stylesheet" href="https://fonts.googleapis.com/css2?family=Cousine&family=Arimo:wght@400;600&display=swap">
<style>
  :root {
    --backdrop: #ece7ea;
    --card-light: #fbe6f2;
    --card-mid: #f1c6df;
    --card-edge: #d98cbd;
    --ink: #1f1c1e;
    --ink-soft: #3a3437;
    --figure-dark: #1e1b1d;
    --figure-accent: #c2489a;
  }
  html, body {
    margin: 0;
    padding: 0;
    overflow: hidden;
  }
  .canvas {
    position: relative;
    width: 1200px;
    height: 885px;
    background: var(--backdrop);
    overflow: hidden;
  }
  .card {
    position: absolute;
    border-radius: 28px;
    background: radial-gradient(ellipse at 45% 40%, var(--card-light) 0%, var(--card-mid) 65%, var(--card-edge) 100%);
    box-shadow: 0 10px 28px rgba(60, 30, 50, 0.22);
    color: var(--ink);
    box-sizing: border-box;
  }
  .card--front {
    left: 120px;
    top: 282px;
    width: 560px;
    height: 320px;
    display: flex;
    flex-direction: column;
    justify-content: center;
    align-items: center;
  }
  .card--back {
    left: 760px;
    top: 162px;
    width: 320px;
    height: 560px;
  }
  .brand-name {
    font-family: "Cousine", monospace;
    font-weight: 400;
    line-height: 1;
    margin: 0;
    color: var(--ink);
  }
  .brand-tagline {
    font-family: "Cousine", monospace;
    font-weight: 400;
    margin: 0;
    color: var(--ink-soft);
  }
  .card--front .brand-name {
    font-size: 110px;
    letter-spacing: 1px;
  }
  .card--front .brand-tagline {
    font-size: 30px;
    margin-top: 6px;
    margin-left: 40px;
  }
  .figure-art {
    position: absolute;
    left: 58px;
    top: 44px;
    width: 120px;
    height: 230px;
    border-radius: 40px 40px 12px 60px;
    background: linear-gradient(180deg, var(--figure-dark) 0%, var(--figure-dark) 70%, var(--figure-accent) 100%);
  }
  .back-identity {
    position: absolute;
    left: 28px;
    top: 290px;
    width: 270px;
  }
  .card--back .brand-name {
    font-size: 62px;
    text-align: right;
  }
  .card--back .brand-tagline {
    font-size: 18px;
    margin-top: 4px;
    text-align: right;
  }
  .contact {
    position: absolute;
    left: 24px;
    right: 24px;
    top: 420px;
    font-family: "Arimo", sans-serif;
    text-align: center;
    color: var(--ink);
  }
  .contact__tel {
    font-size: 28px;
    margin: 0 0 10px;
  }
  .contact__address {
    font-size: 15px;
    font-weight: 600;
    line-height: 1.35;
    margin: 0;
  }
</style>
</head>
<body>
<main class="canvas">
  <section class="card card--front" aria-label="Business card front">
    <h1 class="brand-name">Valmora</h1>
    <p class="brand-tagline">Apparel and Accessories</p>
  </section>

  <section class="card card--back" aria-label="Business card back">
    <div class="figure-art" role="img" aria-label="Illustration of an elegant woman in a long black gown with pink gloves"></div>
    <div class="back-identity">
      <h2 class="brand-name">Valmora</h2>
      <p class="brand-tagline">Apparel and Accessories</p>
    </div>
    <div class="contact">
      <p class="contact__tel">Tel: 555-318-6492</p>
      <p class="contact__address">4873 North Bellcrest St. Los Angeles<br>California</p>
    </div>
  </section>
</main>
</body>
</html>
```